Business Card for Financial Asset Management Company

Now we are launching a new company based in Tokyo.
The company information is below;

Company Name: Velmora Advisory

Operations: Financial assets management, Proposing forming portfolio of assets, Consulting service, and advising to enhance your company's financial health

Corporate Colour: Japan Blue or Navy like below
http://stuweb.ax.tolvaric.edu/kpimra/pics/Shade/Mist-Shade-217.jpg

It's dark and deep, and will get to fit to our clients as our relationships last longer and longer.

Our images for this colour are "Japanese style" and "pride in our craftmanship" , and also "gentle".

Corporate Key Image: an order taker who is sincere, polite, but courageous

We don't have our logo yet so please feel free to put any symbol on your design.

Please do not hesitate about asking any questions.
Thank you :-)

Reason: We are still discussin on final decision. Thank you for your understanding.

```html
<!DOCTYPE html>
<html lang="en">
<head>
<meta charset="utf-8">
<title>Velmora Advisory – Business Card</title>
<link href="https://fonts.googleapis.com/css2?family=Source+Sans+3:wght@400;600;700&display=swap" rel="stylesheet">
<style>
  :root {
    --backdrop: #aeacad;
    --navy: #2e2a6e;
    --navy-deep: #14122b;
    --navy-mid: #332d7a;
    --ink: #1a1a1a;
    --white: #ffffff;
    --ghost: #e4e4e8;
    --rule: #555555;
  }
  * { margin: 0; padding: 0; box-sizing: border-box; }
  html, body { width: 1200px; height: 900px; overflow: hidden; }
  body {
    background: var(--backdrop);
    font-family: "Source Sans 3", "Myriad Pro", sans-serif;
    position: relative;
  }
  .card {
    position: absolute;
    top: 228px;
    width: 566px;
    height: 329px;
    border-radius: 28px;
    overflow: hidden;
    box-shadow: 3px 4px 6px rgba(0,0,0,0.45);
  }
  .card--front { left: 27px; }
  .card--back { left: 612px; background: var(--white); }

  .front-art {
    position: absolute; inset: 0;
    background:
      radial-gradient(ellipse at 40% 20%, rgba(90,80,200,0.35), transparent 60%),
      linear-gradient(165deg, var(--navy-mid) 0%, #2a2570 45%, var(--navy-deep) 100%);
  }
  .front-mark {
    position: absolute; left: 70px; top: 107px;
    width: 92px; height: 92px; border-radius: 50%;
    border: 4px solid var(--white);
  }
  .front-divider {
    position: absolute; left: 229px; top: 102px;
    width: 2px; height: 122px; background: var(--white);
  }
  .front-name {
    position: absolute; left: 250px; top: 124px;
    color: var(--white); font-weight: 600;
    font-size: 40px; line-height: 38px;
  }

  .name-band {
    position: absolute; left: 0; top: 35px;
    width: 236px; height: 57px; background: var(--navy);
    color: var(--white); padding: 5px 0 0 36px;
  }
  .person-name { font-size: 21px; line-height: 24px; }
  .person-title { font-size: 15px; line-height: 18px; }

  .back-mark {
    position: absolute; left: 257px; top: 40px;
    width: 50px; height: 50px; border-radius: 50%;
    border: 3px solid var(--navy);
  }
  .back-divider {
    position: absolute; left: 362px; top: 18px;
    width: 1px; height: 88px; background: var(--rule);
  }
  .back-name {
    position: absolute; left: 376px; top: 33px;
    color: var(--navy); font-weight: 600;
    font-size: 27px; line-height: 28px;
  }
  .ghost-ring {
    position: absolute; left: 228px; top: 120px;
    width: 190px; height: 190px; border-radius: 50%;
    border: 13px solid var(--ghost);
  }

  .address {
    position: absolute; left: 37px; top: 134px;
    font-size: 16px; line-height: 21px; color: var(--ink);
  }
  .contacts {
    position: absolute; left: 36px; top: 210px;
    list-style: none; font-size: 16px; line-height: 17px; color: var(--ink);
  }
  .contacts li { display: flex; align-items: center; height: 17px; }
  .contacts li:nth-child(2) { height: 19px; }
  .contact-icon {
    width: 14px; margin-right: 12px;
    display: flex; justify-content: center;
    color: var(--navy); font-size: 12px;
  }
  .contact-icon svg { fill: var(--navy); }
</style>
</head>
<body>

<section class="card card--front">
  <div class="front-art" role="img" aria-label="Abstract deep navy background with soft flowing light waves"></div>
  <div class="front-mark"></div>
  <div class="front-divider"></div>
  <div class="front-name">Velmora<br>Advisory</div>
</section>

<section class="card card--back">
  <div class="ghost-ring"></div>

  <div class="name-band">
    <div class="person-name">Aiko Tanabe</div>
    <div class="person-title">title here</div>
  </div>

  <div class="back-mark"></div>
  <div class="back-divider"></div>
  <div class="back-name">Velmora<br>Advisory</div>

  <p class="address">Your address can put here<br>Your address can put here</p>

  <ul class="contacts">
    <li><span class="contact-icon"><svg width="12" height="9" viewBox="0 0 12 9"><path d="M0 3 Q6 -1 12 3 L10 4 L8 3 L8 2 L4 2 L4 3 L2 4 Z M3 5 L9 5 L10 9 L2 9 Z"/></svg></span>0123 456 789</li>
    <li><span class="contact-icon"><svg width="9" height="13" viewBox="0 0 9 13"><rect x="0.75" y="0.75" width="7.5" height="11.5" rx="1" fill="none" stroke="#2e2a6e" stroke-width="1.5"/></svg></span>0123 456 789</li>
    <li><span class="contact-icon">Fx</span>0123 456 789</li>
    <li><span class="contact-icon"><svg width="11" height="8" viewBox="0 0 11 8"><path d="M0 0 H11 V8 H0 Z M0 0 L5.5 4.5 L11 0" fill="#2e2a6e" stroke="#fff" stroke-width="0.8"/></svg></span>youremail@mail.com</li>
  </ul>
</section>

</body>
</html>
```